Short fill E liquid label UK. 100ml Nicotine free

Short Fill e liquid label (UK). The BRAND name is "Lumora" (Logo uploaded).Looking to release a new range under the Lumora name. The new range will be called "Glitch". A range of Liquids mixed together. Needs to look cool, stand out and funky but not too crazy. The range will have 10 different flavours so will need these all done, a simple flavour name towards bottom of label will do for this or a different colour for each.Any warnings ( requirements by law) etc and company address/details etc need to have a place on the labels. Basically need to be E liquid compliant label but all are nicotine free so not so many law requirements.Label Size will be 120mm( wide)x 60mm(high), bottle diameter is 41mm .

The 10 flavour names are as follows so will need appropriate colours for each flavour:
Berserker ( a menthol and custard mix )
Fruit loop ( a mixed fruit mix )
Smooth custard ( custard based mix )
Strawberry Shake ( Strawberry milkshake mix )
Cookie Jar ( a cookie based mix )
Black ice ( a liquorice and menthol mix )
Madagascan breeze ( Mainly vanilla based mix )
Choc shake ( chocolate milkshake )
nutter ( a peanut butter and banana mix )
Cool currant ( blackcurrant and menthol mix )

Requirements
Must have
• The info and warnings that need to be on the bottle are as follows:
• signs that need to be on bottle:
• 18+ sign
• Caution sign (!)
• United kingdom flag with" made in the united kingdom written underneath"
• text that needs to be on the bottle:
• Nicotine free eliquid. (in bold lettering )
• Keep out of the reach of children. Always
• read the label before use.
• If swallowed consult a doctor if feeling unwell . In case of contact with eyes consult a doctor.
• Dispose of in a responsible manner.
• Store in a dark place at room temperature.
• Ingredients:
• Vegetable glycerin, Propylene glycol, Flavourings.
• PG/VG ratio 70/30 %

```html
<!DOCTYPE html>
<html lang="en">
<head>
<meta charset="utf-8">
<title>Lumora Glitch – Berserker Short Fill Label</title>
<link rel="stylesheet" href="https://fonts.googleapis.com/css2?family=Lato:wght@400;700;900&family=Montserrat:wght@700;800&display=swap">
<style>
  :root {
    --bg-deep: #0c0c0c;
    --bg-mid: #1d1d1d;
    --ink: #ffffff;
    --ink-dark: #161616;
    --panel: #ffffff;
    --flag-blue: #012169;
    --flag-red: #c8102e;
  }
  * { margin: 0; padding: 0; box-sizing: border-box; }
  html, body { width: 1200px; height: 601px; overflow: hidden; background: var(--bg-deep); }
  .label {
    position: relative;
    width: 1200px;
    height: 601px;
    overflow: hidden;
    color: var(--ink);
    font-family: "Lato", Arial, sans-serif;
    background: radial-gradient(ellipse at 50% 45%, var(--bg-mid) 0%, var(--bg-deep) 70%);
  }
  .block { position: absolute; text-align: center; }
  .heading { font-weight: 700; font-size: 25px; line-height: 1; }
  .copy { font-size: 18px; line-height: 23px; }

  .warnings { left: 35px; top: 66px; width: 330px; }
  .warnings .copy { margin-top: 14px; }

  .badge {
    position: absolute;
    top: 302px;
    width: 78px; height: 78px;
    border-radius: 50%;
    background: var(--panel);
    display: flex; align-items: center; justify-content: center;
    color: var(--ink-dark);
  }
  .badge-age { left: 71px; font-weight: 900; font-size: 30px; }
  .badge-pregnancy { left: 161px; }
  .badge-caution { left: 251px; }
  .badge-caution .outline { fill: none; stroke: var(--ink-dark); stroke-width: 4; stroke-linejoin: round; }
  .badge-caution .mark { fill: var(--ink-dark); }

  .address { left: 35px; top: 422px; width: 330px; }
  .address .copy { margin-top: 14px; }

  .brand-seal {
    position: absolute; left: 504px; top: 57px;
    width: 192px; height: 192px; border-radius: 50%;
    background: var(--panel);
    display: flex; align-items: center; justify-content: center;
    color: var(--ink-dark); font-weight: 900; font-size: 40px;
  }
  .range-rule {
    position: absolute; left: 427px; width: 347px; height: 5px;
    background: var(--ink);
  }
  .range-rule.top { top: 291px; }
  .range-rule.bottom { top: 389px; }
  .range-name {
    position: absolute; left: 400px; top: 303px; width: 400px;
    text-align: center; font-family: "Montserrat", Arial, sans-serif;
    font-weight: 800; font-size: 84px; line-height: 1; letter-spacing: 3px;
  }
  .product-type {
    position: absolute; left: 380px; top: 452px; width: 440px; text-align: center;
    font-family: "Montserrat", Arial, sans-serif; font-weight: 800;
    font-size: 19px; letter-spacing: 4px;
  }
  .volume {
    position: absolute; left: 508px; top: 512px; width: 184px; height: 46px;
    text-align: center; font-weight: 900;
  }
  .volume svg { position: absolute; left: 0; top: 10px; }
  .volume path { fill: none; stroke: var(--ink); stroke-width: 3; }
  .volume .flavour { position: relative; font-size: 20px; line-height: 22px; }
  .volume .amount { position: relative; font-size: 20px; line-height: 24px; }

  .ingredients { left: 850px; top: 70px; width: 302px; }
  .ingredients .copy { margin-top: 20px; }

  .flag { position: absolute; left: 961px; top: 298px; }
  .flag .field { fill: var(--flag-blue); }
  .flag .saltire-white { stroke: var(--ink); stroke-width: 6; }
  .flag .saltire-red { stroke: var(--flag-red); stroke-width: 4; }
  .flag .cross-white { stroke: var(--ink); stroke-width: 10; }
  .flag .cross-red { stroke: var(--flag-red); stroke-width: 6; }

  .origin { position: absolute; left: 846px; top: 373px; width: 310px; text-align: center; font-size: 22px; }
  .code-panel {
    position: absolute; left: 862px; top: 431px; width: 278px; height: 116px;
    background: var(--panel); color: var(--ink-dark);
    display: flex; align-items: center; justify-content: center; font-size: 36px;
  }
</style>
</head>
<body>
<main class="label">
  <section class="block warnings">
    <h2 class="heading">Warnings:</h2>
    <p class="copy">Keep out of the reach of children. Always read the label before use. If swallowed consult a doctor if feeling unwell. In case of contact with eyes consult a doctor. Dispose of in a responsible manner. Store in a dark place at room temperature.</p>
  </section>

  <div class="badge badge-age">18+</div>
  <div class="badge badge-pregnancy" role="img" aria-label="Not for use during pregnancy sign"></div>
  <div class="badge badge-caution" role="img" aria-label="Caution">
    <svg width="54" height="48" viewBox="0 0 54 48" aria-hidden="true">
      <path class="outline" d="M27 4 L51 45 H3 Z"/>
      <rect class="mark" x="24.5" y="17" width="5" height="16" rx="2"/>
      <circle class="mark" cx="27" cy="38.5" r="3"/>
    </svg>
  </div>

  <section class="block address">
    <h2 class="heading">Address:</h2>
    <p class="copy">Lumora Liquids Ltd, Unit 4 Harbour Works, Leeds LS9 8QT, United Kingdom. hello@lumoraliquids.co.uk</p>
  </section>

  <div class="brand-seal">Lumora</div>
  <div class="range-rule top"></div>
  <h1 class="range-name">GLITCH</h1>
  <div class="range-rule bottom"></div>
  <p class="product-type">NICOTINE FREE E-LIQUID</p>

  <div class="volume">
    <svg width="184" height="34" viewBox="0 0 184 34" aria-hidden="true">
      <path d="M12 2 H2 V32 H12 M172 2 H182 V32 H172"/>
    </svg>
    <div class="flavour">Berserker</div>
    <div class="amount">100 ML | 0 Mg</div>
  </div>

  <section class="block ingredients">
    <h2 class="heading">Ingredients:</h2>
    <p class="copy">Vegetable Glycerin,<br>Propylene Glycol,<br>Flavourings.<br>PG/VG ratio 70/30 %</p>
  </section>

  <svg class="flag" width="80" height="40" viewBox="0 0 60 30" role="img" aria-label="United Kingdom flag">
    <clipPath id="flag-area"><path d="M0 0 V30 H60 V0 Z"/></clipPath>
    <clipPath id="flag-diagonals"><path d="M30 15 H60 V30 Z V30 H0 Z H0 V0 Z V0 H60 Z"/></clipPath>
    <g clip-path="url(#flag-area)">
      <path class="field" d="M0 0 V30 H60 V0 Z"/>
      <path class="saltire-white" d="M0 0 L60 30 M60 0 L0 30"/>
      <path class="saltire-red" d="M0 0 L60 30 M60 0 L0 30" clip-path="url(#flag-diagonals)"/>
      <path class="cross-white" d="M30 0 V30 M0 15 H60"/>
      <path class="cross-red" d="M30 0 V30 M0 15 H60"/>
    </g>
  </svg>
  <p class="origin">Made in the United Kingdom</p>
  <div class="code-panel">bar code</div>
</main>
</body>
</html>
```